Roofing Company Modern look

I want a modern and sophisticated look for our roofing business.

Our address is :

5217 Mallow Creek Ln
Orlando, Fl 32825

(407)-583-2196

www.HarborlineRoofsFl.com

I also want to make sure on the back there is a spot to put
Project Manager Name :

Number:

Because the cards will be used by all sales people

Project Manager Name :

Also there are accreditation we have logos are uploaded here as well that I would like maybe on the back of card as well

I also want to highlight our special attributions or trades:

Residential & Commercial
Fully Insured
License # CCC7482913
Insurance Claims
Serving Central Florida Since 1992
Free Estimates

Contact Information for Business Card

Our address is :

5217 Mallow Creek Ln
Orlando, Fl 32825

(407)-583-2196

Project Manager Name :

Residential & Commercial
Fully Insured
License # CCC7482913
Insurance Claims
Free Estimates

Font styles to use
Serif
Sans Serif

Colors
3176b5

Requirements
Must have
• Must have royal blue like my logo grey and black are the colors I like

```html
<!DOCTYPE html>
<html lang="en">
<head>
<meta charset="utf-8">
<title>Harborline Roofing &amp; Gutters – Business Card</title>
<link href="https://fonts.googleapis.com/css2?family=Poppins:wght@400;500;600&display=swap" rel="stylesheet">
<style>
  :root {
    --royal: #2f78c0;
    --ink: #4a4a4f;
    --dark: #3d3d42;
    --card-white: #ffffff;
    --card-black: #0b0b0c;
    --strip: #f3f3f6;
    --stage: #2a2a2c;
    --badge-navy: #1f3f73;
    --badge-red: #c8202a;
    --badge-grey: #8a8d93;
  }
  * { margin: 0; padding: 0; box-sizing: border-box; }
  html, body { width: 1200px; height: 1192px; overflow: hidden; }
  body {
    background: var(--stage);
    font-family: "Poppins", sans-serif;
    position: relative;
  }
  .card {
    position: absolute;
    left: 209px;
    width: 782px;
    height: 448px;
    border-radius: 14px;
    overflow: hidden;
  }
  .card--front { top: 130px; background: var(--card-white); color: var(--ink); }
  .card--back { top: 614px; background: var(--card-black); }

  .front-sheen {
    position: absolute; right: 0; top: 0; width: 220px; height: 100%;
  }
  .holder { position: absolute; left: 50px; top: 50px; }
  .holder__name { font-size: 25px; font-weight: 500; line-height: 1.1; color: var(--dark); }
  .holder__name .first { color: var(--royal); }
  .holder__title { font-size: 19px; line-height: 1.3; }
  .rule { width: 13px; height: 2px; background: var(--royal); position: absolute; left: 50px; }
  .trades { position: absolute; left: 50px; top: 151px; font-size: 19px; line-height: 23.6px; }
  .trades .label { color: var(--royal); }
  .contact { position: absolute; left: 50px; top: 325px; font-size: 19px; line-height: 26.5px; }
  .contact li { list-style: none; display: flex; align-items: center; gap: 8px; }
  .contact svg { width: 15px; height: 15px; fill: var(--royal); flex: none; }
  .divider { position: absolute; left: 391px; top: 361px; width: 2px; height: 37px; background: var(--royal); }
  .address { position: absolute; left: 406px; top: 352px; font-size: 19px; line-height: 24px; display: flex; gap: 6px; }
  .address svg { width: 12px; height: 15px; fill: var(--royal); margin-top: 5px; flex: none; }

  .brand { position: absolute; display: flex; flex-direction: column; align-items: center; color: var(--royal); font-weight: 600; text-align: center; }
  .brand__mark { border-radius: 50%; background: var(--royal); }
  .brand--front { left: 470px; top: 60px; width: 270px; }
  .brand--front .brand__mark { width: 70px; height: 70px; margin-bottom: 14px; }
  .brand--front .brand__name { font-size: 22px; line-height: 1.25; }
  .brand--back { left: 150px; top: 95px; width: 482px; flex-direction: row; justify-content: center; gap: 22px; }
  .brand--back .brand__mark { width: 84px; height: 84px; flex: none; }
  .brand--back .brand__name { font-size: 28px; line-height: 1.2; text-align: left; }

  .site { position: absolute; top: 284px; width: 100%; text-align: center; color: #fff; font-size: 20px; letter-spacing: 1px; }
  .partners { position: absolute; left: 0; top: 332px; width: 100%; height: 116px; background: var(--strip); border-top: 3px solid var(--royal); }
  .partners__label {
    position: absolute; left: 224px; top: -13px; width: 334px; height: 22px;
    background: var(--royal); color: #fff; border-radius: 11px;
    font-size: 18px; line-height: 22px; text-align: center;
  }
  .badge { position: absolute; }
  .badge--a { left: 167px; top: 36px; width: 53px; height: 66px; background: var(--badge-navy); border-radius: 4px; }
  .badge--b { left: 254px; top: 36px; width: 76px; height: 64px; background: var(--badge-navy); clip-path: polygon(50% 0, 100% 30%, 100% 70%, 50% 100%, 0 70%, 0 30%); }
  .badge--c { left: 369px; top: 48px; width: 141px; height: 40px; background: var(--badge-red); }
  .badge--d { left: 538px; top: 36px; width: 76px; height: 66px; background: var(--badge-grey); border-radius: 50%; }
</style>
</head>
<body>

<section class="card card--front">
  <svg class="front-sheen" viewBox="0 0 220 448" preserveAspectRatio="none" aria-hidden="true">
    <path d="M200 70 C130 200 120 330 210 448 L220 448 L220 60 Z" fill="#efeff1"/>
    <path d="M150 448 C200 380 215 330 220 290 L220 448 Z" fill="#e8e8eb"/>
  </svg>

  <div class="holder">
    <p class="holder__name"><span class="first">Martin</span> Ashworth</p>
    <p class="holder__title">Project Manager</p>
  </div>
  <span class="rule" style="top:129px"></span>

  <div class="trades">
    <p><span class="label">License #</span> CCC7482913</p>
    <p>Residential &amp; Commercial</p>
    <p>Fully Insured</p>
    <p>Insurance Claims</p>
    <p>Serving Central Florida Since 1992</p>
    <p>Free Estimates</p>
  </div>
  <span class="rule" style="top:309px"></span>

  <ul class="contact">
    <li><svg viewBox="0 0 24 24"><path d="M6.6 10.8a15.1 15.1 0 0 0 6.6 6.6l2.2-2.2a1 1 0 0 1 1-.25 11.4 11.4 0 0 0 3.6.57 1 1 0 0 1 1 1V20a1 1 0 0 1-1 1A17 17 0 0 1 3 4a1 1 0 0 1 1-1h3.5a1 1 0 0 1 1 1c0 1.25.2 2.45.57 3.57a1 1 0 0 1-.25 1z"/></svg>(407)-583-2196</li>
    <li><svg viewBox="0 0 24 24"><path d="M2 5h20v14H2z M2 5l10 8 10-8" fill="none" stroke="#2f78c0" stroke-width="2.5"/></svg>HarborlineRoofsFl@gmail.com</li>
    <li><svg viewBox="0 0 24 24"><circle cx="12" cy="12" r="10"/><path d="M2 12h20M12 2c3 3 3 17 0 20M12 2c-3 3-3 17 0 20" stroke="#fff" stroke-width="1.5" fill="none"/></svg>www.HarborlineRoofsFl.com</li>
  </ul>
  <span class="divider"></span>
  <div class="address">
    <svg viewBox="0 0 12 16"><path d="M6 0a6 6 0 0 0-6 6c0 4.5 6 10 6 10s6-5.5 6-10a6 6 0 0 0-6-6zm0 8.5A2.5 2.5 0 1 1 6 3.5a2.5 2.5 0 0 1 0 5z"/></svg>
    <p>5217 Mallow Creek Ln<br>Orlando, Fl 32825</p>
  </div>

  <div class="brand brand--front">
    <span class="brand__mark"></span>
    <p class="brand__name">HARBORLINE<br>ROOFING &amp; GUTTERS INC.</p>
  </div>
</section>

<section class="card card--back">
  <div class="brand brand--back">
    <span class="brand__mark"></span>
    <p class="brand__name">HARBORLINE<br>ROOFING &amp; GUTTERS LLC.</p>
  </div>
  <p class="site">www.harborlineroofsfl.com</p>

  <div class="partners">
    <p class="partners__label">Our Accreditations &amp; Partners</p>
    <span class="badge badge--a" role="img" aria-label="Accredited business rating badge"></span>
    <span class="badge badge--b" role="img" aria-label="Shingle applicator certification badge"></span>
    <span class="badge badge--c" role="img" aria-label="Authorized roofing contractor badge"></span>
    <span class="badge badge--d" role="img" aria-label="Screened and approved listing badge"></span>
  </div>
</section>

</body>
</html>
```